Visitenkarten-Design für Forschungs- und Beratungsunternehmen
Zielgruppe
*Fervolia' ist ein Forschungs- und Beratungsunternehmen für Lebensmittelwirkungen. Unsere Angebote sind: Vorträge, Workshops, Seminare und Coaching. Die Zielgruppen sind Pädagogen, Mediziner, Psychologen u.a.m.
Aufgabenstellung
Bei Bedarf kann die Gestaltung der Visitenkarte auch auf die Rückseite ausgedehnt werden.

```html
<!DOCTYPE html>
<html lang="de">
<head>
<meta charset="utf-8">
<title>Fervolia – Visitenkarte</title>
<link rel="stylesheet" href="https://fonts.googleapis.com/css2?family=Poppins:wght@400;500;700&display=swap">
<style>
  :root {
    --backdrop: #a4a9ae;
    --card-white: #f4f4f4;
    --card-navy: #1b2a3d;
    --ink: #1e1e1e;
    --ink-soft: #3a3a3a;
    --on-navy: #e9edf2;
    --accent-blue: #1f86d0;
    --tone-orange: rgba(240,138,18,.45);
    --tone-magenta: rgba(196,42,140,.45);
    --tone-blue: rgba(31,134,208,.45);
  }
  * { box-sizing: border-box; margin: 0; padding: 0; }
  html, body { width: 1200px; height: 900px; overflow: hidden; }
  body {
    background: var(--backdrop);
    font-family: "Poppins", sans-serif;
    display: flex;
    align-items: center;
    justify-content: center;
    gap: 40px;
  }
  .card {
    position: relative;
    width: 540px;
    height: 350px;
    border-radius: 3px;
    box-shadow: 0 10px 24px rgba(0,0,0,.22);
    overflow: hidden;
  }

  /* Back side */
  .card--back { background: var(--card-navy); }
  .back-decoration {
    position: absolute;
    left: 0; top: 0;
    width: 360px; height: 100%;
    background: linear-gradient(160deg, var(--tone-orange) 0%, var(--tone-blue) 45%, var(--tone-magenta) 100%);
    -webkit-mask-image: linear-gradient(90deg, #000 40%, transparent 100%);
    mask-image: linear-gradient(90deg, #000 40%, transparent 100%);
  }
  .back-brand {
    position: absolute;
    right: 44px; bottom: 52px;
    display: flex; align-items: center; gap: 12px;
    color: var(--on-navy);
  }

  /* Brand mark */
  .brand-dot {
    width: 16px; height: 16px; border-radius: 50%;
    background: var(--accent-blue);
  }
  .brand-name {
    font-size: 28px; font-weight: 400; letter-spacing: .04em; line-height: 1;
  }

  /* Front side */
  .card--front { background: var(--card-white); color: var(--ink); }
  .front-brand {
    position: absolute; left: 40px; top: 44px;
    display: flex; align-items: center; gap: 12px;
    color: var(--ink-soft);
  }
  .person {
    position: absolute; left: 300px; top: 46px;
  }
  .person-name { font-size: 18px; font-weight: 700; line-height: 1.2; }
  .person-role { font-size: 13px; color: var(--ink-soft); letter-spacing: .02em; }
  .contact {
    position: absolute; left: 290px; top: 178px;
    display: grid; grid-template-columns: 26px auto;
    row-gap: 4px;
    font-size: 14px; letter-spacing: .02em;
  }
  .contact dt { font-size: 12px; color: var(--ink-soft); padding-top: 2px; }
  .contact dd { margin: 0; }
  .hours {
    position: absolute; left: 40px; bottom: 48px;
    font-size: 14px; letter-spacing: .02em;
  }
  .hours strong { font-weight: 700; }
</style>
</head>
<body>
  <section class="card card--back" aria-label="Rückseite">
    <div class="back-decoration" role="img" aria-label="Farbige Ring-Illustration in Orange, Blau und Magenta"></div>
    <div class="back-brand">
      <span class="brand-dot"></span>
      <span class="brand-name">Fervolia</span>
    </div>
  </section>

  <section class="card card--front" aria-label="Vorderseite">
    <div class="front-brand">
      <span class="brand-dot"></span>
      <span class="brand-name">Fervolia</span>
    </div>
    <div class="person">
      <p class="person-name">Matthias Wendler</p>
      <p class="person-role">Geschäftsführer</p>
    </div>
    <dl class="contact">
      <dt>A:</dt><dd>Lindenweg 14<br>CH-4410 Liestal</dd>
      <dt>T:</dt><dd>+41 61 555 24 80</dd>
      <dt>E:</dt><dd>info@fervolia.ch</dd>
      <dt>W:</dt><dd>www.fervolia.ch</dd>
    </dl>
    <p class="hours"><strong>MO – FR</strong> 10.00 h – 19.00 h</p>
  </section>
</body>
</html>
```